Wren of Fabrics relaunch: brand, logo and website redesign

Wren of Fabrics www.wrenoffabrics.com is relaunching to focus on empowering style advice, e books and courses.
We need a new logo, brand identity and website which reflects this change.
The structure of the site and pages have been completed http://dev1.wrenoffabrics.com/
but we need to update the brand look and feel
Please read the full brief, uploaded, before submitting your designs.

Target Market(s)

Women, primarily aged 28-45, English speaking USA and UK
Ambitious and determined. Looking for solutions. Open to self-improvement.
Maybe not as confident with style and body image as other parts of their life.

Logo Text

Brand name Wren of Fabrics Strapline version 1: Unlock your personal best Strapline version 2: Unlock better Logo/graphical icon for use with/without text

Number of Pages Required

3 page

Font styles to use
Sans Serif

Requirements
Must have
• 1. Web designs for home page, a channel page and advice page (see attached brief)
Web designs must be consistent with new website design navigation, and page structure http://dev1.wrenoffabrics.com/
2. Web style guide to include colour palettes/system; web fonts, icons, illustrations and guidelines/examples free stock photography. see Mindmap upload for example of colour pallette we like.
Nice to have
• Ebook front covers
Quiz promotions
Course promotions
Other web pages
Social media pages eg Pagebook, Snapgrid,Chirpline
Should not have
• Paid photography or photos where don’t have the rights

```html
<!DOCTYPE html>
<html lang="en">
<head>
<meta charset="utf-8">
<title>Wren of Fabrics — Your Personal Stylist</title>
<link href="https://fonts.googleapis.com/css2?family=Montserrat:wght@400;500;600;700&family=Poppins:wght@500;600&display=swap" rel="stylesheet">
<style>
:root{
  --green:#5ec11c;
  --green-light:#c6ea2b;
  --orange:#ef5b1d;
  --navy:#2f425a;
  --navy-dark:#1f2e42;
  --ink:#2a2a2a;
  --muted:#555;
  --mist:#dde3eb;
  --white:#fff;
}
*{margin:0;padding:0;box-sizing:border-box}
html,body{width:1200px;height:5013px;overflow:hidden}
body{position:relative;font-family:'Montserrat',sans-serif;color:var(--ink);background:var(--white)}
.abs{position:absolute}
.photo{position:absolute}
.btn{position:absolute;background:var(--orange);color:var(--white);font-size:12px;font-weight:500;display:flex;align-items:center;justify-content:center;text-transform:uppercase;letter-spacing:.2px}
.section-title{position:absolute;left:0;width:1200px;text-align:center;font-weight:500;font-size:40px}
.section-sub{position:absolute;left:0;width:1200px;text-align:center;font-size:17px}

/* header */
.site-header{top:0;left:0;width:1200px;height:122px;background:var(--white)}
.brand{left:145px;top:36px;display:flex;align-items:center;gap:12px;font-size:28px;font-weight:700;color:var(--navy)}
.brand-dot{width:22px;height:22px;border-radius:50%;background:var(--green)}
.search{left:679px;top:18px;width:211px;height:34px;border:1px solid #999;font-size:11px;color:#999;padding:9px 14px}
.search svg{position:absolute;right:10px;top:9px}
.account{left:948px;top:18px;width:34px;height:34px;border-radius:50%;background:var(--navy-dark)}
.cart{left:1020px;top:18px;width:36px;height:36px;border-radius:50%;background:var(--orange)}
.cart-count{left:1008px;top:14px;width:18px;height:18px;border-radius:50%;background:#e6d100;font-size:10px;text-align:center;line-height:18px}
.main-nav{left:418px;top:82px;display:flex;gap:38px;font-size:14px}
.main-nav .current{color:var(--green)}

/* hero */
.hero{top:122px;left:0;width:1200px;height:610px}
.hero-title{left:415px;top:333px;width:370px;height:62px;background:var(--green);color:var(--white);font-family:'Poppins',sans-serif;font-weight:600;font-size:32px;display:flex;align-items:center;justify-content:center}
.hero-arrow{top:348px;width:38px;height:38px;border-radius:50%;background:#111;display:flex;align-items:center;justify-content:center}

/* about */
.about-title{left:144px;top:858px;font-size:40px;font-weight:500}
.about-lead{left:144px;top:926px;font-size:15px}
.about-text{left:144px;top:960px;width:575px;font-size:13.5px;line-height:29px;color:var(--muted)}

/* style advice */
.advice{top:1228px;left:0;width:1200px;height:924px;background:var(--navy)}
.tile{position:absolute;width:298px;height:297px}
.tile-label{position:absolute;left:0;bottom:0;width:100%;height:36px;background:linear-gradient(90deg,var(--green),var(--green-light));color:#1d2b12;font-size:15px;font-weight:500;display:flex;align-items:center;justify-content:center}

/* courses */
.course{position:absolute;top:2350px;width:300px;text-align:center}
.course h3{font-size:19px;font-weight:500;color:var(--green);margin-top:96px}
.course p{font-size:12.5px;line-height:24px;margin-top:14px;color:#333}
.divider{position:absolute;top:2350px;width:1px;height:320px;background:#bbb}

/* banner */
.banner{top:2750px;left:0;width:1200px;height:480px;background:var(--mist)}
.banner-title{left:620px;top:2834px;width:460px;text-align:center;font-size:40px;line-height:60px;font-weight:500}
.banner-text{left:620px;top:2978px;width:460px;text-align:center;font-size:15px;line-height:30px}

/* ebooks */
.ebook-title{left:493px;top:3350px;font-size:40px;font-weight:500}
.ebook-offer{left:493px;top:3413px;font-size:25px;color:var(--green)}
.ebook-text{left:493px;top:3456px;width:580px;font-size:13.5px;line-height:26px}
.store-badge{position:absolute;top:3520px;height:47px;border-radius:6px;background:#111}

/* blog */
.blog{top:3728px;left:0;width:1200px;height:530px;background:var(--navy)}
.post{position:absolute;top:3873px;width:298px;height:304px;background:var(--white)}
.post .photo{left:0;top:0;width:298px;height:192px}
.post-date{position:absolute;right:0;top:136px;width:52px;height:56px;background:var(--green);color:var(--white);text-align:center;font-weight:700;font-size:30px;line-height:32px}
.post-date span{display:block;font-size:18px;font-weight:400;line-height:20px}
.post p{position:absolute;left:24px;top:212px;width:256px;font-size:14px;line-height:24px;color:#333}
.blog-arrow{position:absolute;top:4016px}

/* gallery */
.gallery-title{left:0;top:4330px;width:1200px;text-align:center;font-size:42px;font-weight:500}

/* newsletter */
.newsletter{top:4660px;left:0;width:1200px;height:235px;background:linear-gradient(90deg,var(--green),var(--green-light))}
.news-title{top:4700px;color:#222;font-size:42px}
.news-sub{top:4758px;font-size:14px;color:#222}
.news-form{left:360px;top:4795px;width:478px;height:44px;background:var(--white);border:2px solid #eee;font-size:15px;color:#999;padding:11px 14px}
.news-btn{left:740px;top:4801px;width:92px;height:32px}

/* footer */
.site-footer{top:4895px;left:0;width:1200px;height:118px;background:var(--navy-dark);color:#ccd}
.footer-links{left:144px;top:4935px;font-size:11px;word-spacing:4px}
.copyright{left:144px;top:4967px;font-size:11px}
.social{position:absolute;top:4938px;width:22px;height:22px;border-radius:50%;background:#8c96a6}
</style>
</head>
<body>

<header class="abs site-header">
  <div class="abs brand"><span class="brand-dot"></span>Wren of Fabrics</div>
  <div class="abs search">Search
    <svg width="14" height="14" viewBox="0 0 14 14"><circle cx="6" cy="6" r="4.5" fill="none" stroke="#111" stroke-width="2"/><line x1="9.3" y1="9.3" x2="13" y2="13" stroke="#111" stroke-width="2"/></svg>
  </div>
  <div class="abs account"><svg width="34" height="34" viewBox="0 0 34 34"><circle cx="17" cy="13" r="5" fill="#fff"/><path d="M9 25a8 7 0 0 1 16 0z" fill="#fff"/></svg></div>
  <div class="abs cart"><svg width="36" height="36" viewBox="0 0 36 36"><path d="M11 12h3l2 9h8l2-7H15" fill="none" stroke="#fff" stroke-width="2"/><circle cx="17" cy="24" r="1.5" fill="#fff"/><circle cx="23" cy="24" r="1.5" fill="#fff"/></svg></div>
  <div class="abs cart-count">0</div>
  <nav class="abs main-nav"><span class="current">Home</span><span>About</span><span>Advice</span><span>Courses</span><span>Quizzes</span><span>Ebooks</span><span>Blog</span><span>Contact</span></nav>
</header>

<section class="abs hero">
  <svg width="1200" height="610" viewBox="0 0 1200 610" class="abs" style="left:0;top:0">
    <polygon points="0,500 600,610 1200,495 1200,485 600,585 0,490" fill="#5ec11c"/>
    <polygon points="0,0 1200,0 1200,485 600,585 0,490" fill="#b9aca0" role="img" aria-label="Woman choosing clothes in an open wardrobe"/>
  </svg>
  <div class="abs hero-title">Your Personal Stylist</div>
  <div class="abs hero-arrow" style="left:56px"><svg width="14" height="14" viewBox="0 0 14 14"><path d="M9 2L4 7l5 5" fill="none" stroke="#fff" stroke-width="2.5"/></svg></div>
  <div class="abs hero-arrow" style="left:1103px"><svg width="14" height="14" viewBox="0 0 14 14"><path d="M5 2l5 5-5 5" fill="none" stroke="#fff" stroke-width="2.5"/></svg></div>
</section>

<section>
  <h2 class="abs about-title">About Us</h2>
  <p class="abs about-lead">Wren of Fabrics was founded by Marina Keller and Daniel Ashworth.</p>
  <p class="abs about-text">To make it easy for you look and feel your best by creating a visual balance and colour harmony in your look. To help you save you money by advising you how to buy the clothes you will wear rather than the ones that stay in your wardrobe. Cost per use is more important than cost per item.</p>
  <div class="btn" style="left:144px;top:1096px;width:96px;height:39px">Read more</div>
  <div class="photo" role="img" aria-label="Portrait of a stylist in a blue blouse" style="left:770px;top:770px;width:290px;height:458px;background:linear-gradient(180deg,#f1f1f3,#c9ccd6 40%,#2d3d8a 70%,#273045)"></div>
</section>

<section class="abs advice">
  <h2 class="section-title" style="top:68px;color:#fff">Style Advice</h2>
  <p class="section-sub" style="top:132px;color:#fff">WHAT and HOW TO WEAR</p>
</section>
<div class="tile" style="left:144px;top:1403px"><div class="photo" role="img" aria-label="Women with different body shapes" style="inset:0;background:linear-gradient(135deg,#d9c7b5,#8c6c58)"></div><div class="tile-label">The Guide to Body Shapes</div></div>
<div class="tile" style="left:451px;top:1403px"><div class="photo" role="img" aria-label="Women in neutral underwear" style="inset:0;background:linear-gradient(135deg,#e6e1dc,#a48a78)"></div><div class="tile-label">Know your best Colours</div></div>
<div class="tile" style="left:758px;top:1403px"><div class="photo" role="img" aria-label="Women wearing jeans" style="inset:0;background:linear-gradient(135deg,#eceae7,#7a8aa4)"></div><div class="tile-label">The Guide to Jeans</div></div>
<div class="tile" style="left:144px;top:1710px"><div class="photo" role="img" aria-label="Bride among wedding dresses" style="inset:0;background:linear-gradient(135deg,#f4f2ef,#cfc7bc)"></div><div class="tile-label">Wedding style &amp; fashion</div></div>
<div class="tile" style="left:451px;top:1710px"><div class="photo" role="img" aria-label="Legs in black hosiery" style="inset:0;background:linear-gradient(135deg,#cfc6bd,#2c2727)"></div><div class="tile-label">The Guide to Hosiery</div></div>
<div class="tile" style="left:758px;top:1710px"><div class="photo" role="img" aria-label="Tape measure around a waist" style="inset:0;background:linear-gradient(135deg,#d3c3b6,#8d7669)"></div><div class="tile-label">Measurement Guides</div></div>
<div class="btn" style="left:508px;top:2035px;width:182px;height:38px;font-size:11px">View all style advices</div>

<section>
  <h2 class="section-title" style="top:2222px">Courses</h2>
  <p class="section-sub" style="top:2288px">INTERACTIVE STYLING TOOLS AND ADVICE</p>
  <div class="divider" style="left:446px"></div>
  <div class="divider" style="left:753px"></div>
  <div class="course" style="left:143px">
    <svg class="abs" style="left:120px;top:6px" width="60" height="80" viewBox="0 0 60 80"><g fill="none" stroke="#222" stroke-width="2"><circle cx="30" cy="10" r="7"/><path d="M20 22h20l-4 22h-12z"/><path d="M24 44l-3 30M36 44l3 30M20 24l-10 16M40 24l10 16"/></g></svg>
    <h3>Personalise your model</h3>
    <p>Choose your<br>Body shape<br>Skin colour<br>Face features<br>Hair colour and style</p>
  </div>
  <div class="course" style="left:450px">
    <svg class="abs" style="left:114px;top:6px" width="72" height="80" viewBox="0 0 72 80"><g fill="none" stroke="#222" stroke-width="2"><path d="M28 4v12M44 4v12"/><path d="M26 16h20l-3 18h-14z"/><path d="M29 34L8 74h56L43 34"/></g></svg>
    <h3>Discover your styles</h3>
    <p>Try on 1000's of styles<br>Stylist recommendations</p>
  </div>
  <div class="course" style="left:757px">
    <svg class="abs" style="left:116px;top:6px" width="70" height="80" viewBox="0 0 70 80"><g fill="none" stroke="#222" stroke-width="2"><rect x="6" y="6" width="18" height="16"/><rect x="26" y="12" width="18" height="16"/><rect x="46" y="2" width="18" height="16"/><path d="M26 34h14v16h10v26H30l-8-16 4-10z"/></g></svg>
    <h3>Create and share looks</h3>
    <p>Create the looks which flatter you and share<br>with friends</p>
  </div>
  <div class="btn" style="left:244px;top:2628px;width:96px;height:38px">Read more</div>
  <div class="btn" style="left:552px;top:2628px;width:96px;height:38px">Read more</div>
  <div class="btn" style="left:859px;top:2628px;width:96px;height:38px">Read more</div>
</section>

<section class="abs banner">
  <div class="photo" role="img" aria-label="Woman holding up knitted jumpers beside a clothes rail" style="left:0;top:0;width:620px;height:480px;background:linear-gradient(90deg,#d7d0c8,#e9e4df 50%,#cdbfb0)"></div>
</section>
<h2 class="abs banner-title">Wren of Fabrics, your personal stylist</h2>
<p class="abs banner-text">Style advice, styling tools and shopping recommendations. Take the fast and fun Style Quiz to discover your unique style DNA</p>
<div class="btn" style="left:772px;top:3094px;width:158px;height:37px;font-size:11px">Take the style quiz</div>

<section>
  <div class="photo" role="img" aria-label="Smiling woman holding a tablet" style="left:145px;top:3260px;width:305px;height:468px;background:linear-gradient(180deg,#f3f3f3,#d9c2a8 35%,#9ad0c4 70%,#a9d7cc)"></div>
  <h2 class="abs ebook-title">Ebooks</h2>
  <p class="abs ebook-offer">20% Offer Now</p>
  <p class="abs ebook-text">DRESS WELL, Your Personal Stylist, will show you how to create the illusion of a perfect figure whatever your shape.</p>
  <div class="store-badge" style="left:496px;width:100px"></div>
  <div class="store-badge" style="left:612px;width:168px"></div>
  <div class="btn" style="left:496px;top:3595px;width:96px;height:37px">Read more</div>
</section>

<section class="abs blog">
  <h2 class="section-title" style="top:66px;color:#fff">Blog</h2>
</section>
<svg class="blog-arrow" style="left:56px" width="20" height="30" viewBox="0 0 20 30"><path d="M15 3L4 15l11 12" fill="none" stroke="#9aa6b6" stroke-width="2.5"/></svg>
<svg class="blog-arrow" style="left:1124px" width="20" height="30" viewBox="0 0 20 30"><path d="M5 3l11 12L5 27" fill="none" stroke="#9aa6b6" stroke-width="2.5"/></svg>
<article class="post" style="left:144px"><div class="photo" role="img" aria-label="Woman in sunglasses on a city street" style="background:linear-gradient(135deg,#b59a80,#e7ddd2)"></div><div class="post-date">08<span>OCT</span></div><p>Phasellus nisl tellus condimentum vitae faucibus in sollicitudin vel metus euismod.</p></article>
<article class="post" style="left:451px"><div class="photo" role="img" aria-label="Woman in a grey dress against a teal wall" style="background:linear-gradient(135deg,#2d6e66,#4f8c80)"></div><div class="post-date">08<span>OCT</span></div><p>Curabitur ac elit leo. In eleifend dui tellus, in scelerisque elit porttitor lacinia nulla volutpat purus.</p></article>
<article class="post" style="left:758px"><div class="photo" role="img" aria-label="Woman in a floral top in an old town" style="background:linear-gradient(135deg,#a87f5e,#d9b8a0)"></div><div class="post-date">08<span>OCT</span></div><p>Vivamus volutpat eu sapien quis tempus. Aenean feugiat viverra lorem ac sagittis.</p></article>

<section>
  <h2 class="abs gallery-title">Snapgrid</h2>
  <div class="photo" role="img" aria-label="Woman in a camel trench dress" style="left:144px;top:4403px;width:176px;height:175px;background:linear-gradient(135deg,#e7ddd4,#a67a5c)"></div>
  <div class="photo" role="img" aria-label="Woman against a colourful painted wall" style="left:328px;top:4403px;width:176px;height:175px;background:linear-gradient(135deg,#e6c23a,#d94a6b 50%,#3a8fc7)"></div>
  <div class="photo" role="img" aria-label="Woman in a grey coat on a street" style="left:512px;top:4403px;width:176px;height:175px;background:linear-gradient(135deg,#bcb8b2,#4a4a4a)"></div>
  <div class="photo" role="img" aria-label="Woman in a brown outfit on a street" style="left:697px;top:4403px;width:176px;height:175px;background:linear-gradient(135deg,#d9ccc0,#8c5a44)"></div>
  <div class="photo" role="img" aria-label="Woman in a dark outfit by a building" style="left:881px;top:4403px;width:175px;height:175px;background:linear-gradient(135deg,#9a9a9a,#3c3c3c)"></div>
</section>

<section class="abs newsletter"></section>
<h2 class="section-title news-title">Subscribe to our newsletter</h2>
<p class="section-sub news-sub">Receive regular email updates on the season's hottest look, our latest arrivals and more.</p>
<div class="abs news-form">Email Address</div>
<div class="btn news-btn" style="font-size:11px">Subscribe</div>

<footer class="abs site-footer"></footer>
<p class="abs footer-links" style="color:#ccd">Home | About | Advice | Courses | Quizzes | Ebooks | Blog | Contact</p>
<p class="abs copyright" style="color:#ccd">Copyright © 2020 Wren of Fabrics. All rights reserved.</p>
<span class="social" style="left:844px"></span>
<span class="social" style="left:888px"></span>
<span class="social" style="left:932px"></span>
<span class="social" style="left:976px"></span>
<span class="social" style="left:1034px"></span>

</body>
</html>
```